SaaS Early tech startup business card design

Unique design for experience ecommerce platform company. the business cards will be used by executive members. conformance with color code is required.

```html
<!DOCTYPE html>
<html lang="en">
<head>
<meta charset="utf-8">
<title>Velto – Business Card</title>
<link href="https://fonts.googleapis.com/css2?family=Montserrat:wght@400;500;700;800&display=swap" rel="stylesheet">
<style>
  :root {
    --stage: #2a2a2e;
    --card-white: #ffffff;
    --card-navy: #1e1f35;
    --brand-blue: #1a6a9a;
    --brand-teal: #1fb89a;
    --ink: #23242c;
  }
  * { box-sizing: border-box; margin: 0; padding: 0; }
  html, body {
    width: 1200px; height: 900px; overflow: hidden;
    background: var(--stage);
    font-family: "Montserrat", sans-serif;
  }
  .stage {
    width: 1200px; height: 900px;
    display: flex; flex-direction: column;
    align-items: center; justify-content: center; gap: 60px;
  }
  .card {
    width: 560px; height: 320px;
    border-radius: 18px;
    position: relative; overflow: hidden;
  }
  .card--front { background: var(--card-white); }
  .card--front::after {
    content: ""; position: absolute; left: 0; right: 0; bottom: 0; height: 6px;
    background: linear-gradient(90deg, var(--brand-blue), var(--brand-teal));
  }
  .identity { position: absolute; left: 36px; top: 58px; }
  .identity__name {
    font-weight: 700; font-size: 22px; letter-spacing: 2px;
    color: var(--brand-blue); text-transform: uppercase;
  }
  .identity__role { font-size: 13px; color: var(--ink); margin-top: 2px; }
  .divider {
    position: absolute; left: 36px; right: 40px; top: 118px;
    height: 1px; background: var(--brand-teal);
  }
  .contacts {
    position: absolute; left: 36px; top: 134px;
    list-style: none; font-size: 12.5px; color: var(--ink); line-height: 19px;
  }
  .contacts li { display: flex; align-items: center; gap: 8px; }
  .contacts svg { width: 11px; height: 11px; fill: var(--brand-blue); flex: none; }
  .address {
    position: absolute; right: 40px; bottom: 34px;
    font-size: 13px; color: var(--ink); text-align: right; line-height: 18px;
  }
  .wordmark {
    font-weight: 800; color: var(--brand-teal); letter-spacing: -1px; line-height: 1;
  }
  .card--front .wordmark {
    position: absolute; right: 40px; top: 36px; font-size: 60px;
  }
  .card--back {
    background: var(--card-navy);
    display: flex; align-items: center; justify-content: center;
  }
  .card--back .wordmark { font-size: 120px; }
</style>
</head>
<body>
<main class="stage">
  <section class="card card--front" aria-label="Business card front">
    <div class="wordmark">velto</div>
    <div class="identity">
      <h1 class="identity__name">Marta Okafor</h1>
      <p class="identity__role">Managing Director</p>
    </div>
    <div class="divider"></div>
    <ul class="contacts">
      <li><svg viewBox="0 0 12 12"><path d="M2.5 1h2l1 3-1.3 1a6 6 0 0 0 2.8 2.8l1-1.3 3 1v2c0 .6-.4 1-1 1A10 10 0 0 1 1.5 2c0-.6.4-1 1-1z"/></svg>03 5550 1472</li>
      <li><svg viewBox="0 0 12 12"><path d="M3.5 0h5c.6 0 1 .4 1 1v10c0 .6-.4 1-1 1h-5c-.6 0-1-.4-1-1V1c0-.6.4-1 1-1zm.5 1.5v7.5h4V1.5z"/></svg>0400 555 872</li>
      <li><svg viewBox="0 0 12 12"><path d="M0 2h12v8H0zm1 1v.3l5 3.2 5-3.2V3z"/></svg>hello@veltocloud.com</li>
      <li><svg viewBox="0 0 12 12"><path d="M6 0a6 6 0 1 0 0 12A6 6 0 0 0 6 0zm0 1.2c.7.8 1.2 2.4 1.3 4.2H4.7C4.8 3.6 5.3 2 6 1.2zM4.7 6.6h2.6c-.1 1.8-.6 3.4-1.3 4.2-.7-.8-1.2-2.4-1.3-4.2z"/></svg>www.veltocloud.com</li>
    </ul>
    <address class="address">Riverbend, Halloway QA<br>Marlow Field Park, 2741</address>
  </section>

  <section class="card card--back" aria-label="Business card back">
    <div class="wordmark">velto</div>
  </section>
</main>
</body>
</html>
```